Indonesian B2B Company (Bawo Ingredients) - Stationery Design

Bawo Ingredients needs a corporate, bold and professional-looking stationery design.

Bawo Ingredients is a new Indonesian company manufacturing, marketing and distributing various ingredients / raw materials such as flavours, fragrance, colours, sweeteners, preservatives for the food & beverage, pharmaceutical, personal care and other household goods industries.

It is a business to business (B2B) company as we supply various natural and synthetic raw materials to various consumer goods manufacturers. We therefore need a logo/identity with corporate and industrial style.

Bawo Ingredients is a startup company which belongs to a larger Tunas Mekar group of companies (http://tunasmekar.examplebiz.net/about) that focuses in the mining, petroleum and energy businesses. Bawo Ingredients would like to focus in providing good quality, safe, reliable and affordable ingredients for the industries. Our tagline is "Quality Materials, Reliable Supply"
Updates

We have updated some information including our requirements and contact details to be shown in the stationery. Please check the project brief.

Regards,

Bawo Ingredients

Target Market(s)

Manufacturers of food & beverages, personal care, pharmaceutical and other FMCG factories.

Industry/Entity Type

Business

Requirements
Must have
• Smart, professional and corporate touches in the stationery designs. We require designs for:
1. Letterhead
2. Envelope (with and without window)
3. Name card
4. Powerpoint presentation template
5. CD label
6. Small memo / with compliments card

Contact details:

Company name:
PT Bawo Ingredients

Address:
Ruko Puri Lestari Selatan, Blok F07 no: 11-12
Sunter Jaya Utara, 14350
Indonesia

Tel:+62 21 638 2097
Fax:+62 21 638 2096
Email: info@bawo-ingredients.co.id
Website: www.bawo-ingredients.co.id

```html
<!DOCTYPE html>
<html lang="en">
<head>
<meta charset="utf-8">
<title>Bawo – Stationery</title>
<link href="https://fonts.googleapis.com/css2?family=Barlow:wght@400;500;600&display=swap" rel="stylesheet">
<style>
  :root {
    --brand-red: #d2202a;
    --brand-red-dark: #a8161e;
    --brand-orange: #f5a91f;
    --ink: #4a4a4a;
    --ink-strong: #3a3a3a;
    --ink-soft: #8a8a8a;
    --paper: #ffffff;
    --backdrop: #d9d6d1;
    --rule: #cfcfcf;
  }
  * { box-sizing: border-box; margin: 0; padding: 0; }
  html, body { width: 1200px; height: 900px; overflow: hidden; }
  body {
    background: var(--backdrop);
    font-family: "Barlow", Arial, sans-serif;
    color: var(--ink);
    position: relative;
  }
  address { font-style: normal; }
  .sheet {
    position: absolute;
    background: var(--paper);
    box-shadow: 0 2px 6px rgba(0,0,0,.18);
    overflow: hidden;
  }

  /* Brand lockup */
  .brand { position: absolute; }
  .brand-row { display: flex; align-items: center; gap: 7px; }
  .brand-mark { width: 14px; height: 14px; background: var(--brand-red); flex: none; }
  .brand-name { color: var(--ink-strong); font-weight: 600; letter-spacing: 2px; white-space: nowrap; }
  .brand-tagline { color: var(--ink-soft); font-weight: 400; white-space: nowrap; margin-top: 3px; }

  .corner-square { position: absolute; background: var(--brand-red); }

  .band { position: absolute; left: 0; right: 0; bottom: 0; display: flex; }
  .band-orange { background: var(--brand-orange); }
  .band-red { background: var(--brand-red); flex: 1; }

  /* Letterhead */
  .letterhead { left: 50px; top: 102px; width: 495px; height: 701px; }
  .letterhead .brand { left: 34px; top: 82px; }
  .letterhead .brand-name { font-size: 20px; }
  .letterhead .brand-tagline { font-size: 9px; margin-left: 21px; }
  .letterhead-contact {
    position: absolute; left: 318px; top: 20px; width: 160px; padding-left: 10px;
    border-left: 1px solid var(--brand-orange);
    font-size: 8.5px; line-height: 1.5; text-align: right; white-space: nowrap;
  }
  .letterhead-contact .company { color: var(--brand-red); font-weight: 600; margin-bottom: 12px; font-size: 9px; }
  .letterhead-contact .gap { height: 12px; }
  .letterhead .corner-square { right: 26px; bottom: 26px; width: 44px; height: 44px; }
  .letterhead .band { height: 12px; }
  .letterhead .band-orange { width: 83px; }

  /* Business cards */
  .card { top: 123px; width: 210px; height: 117px; border-radius: 7px; }
  .card-front { left: 654px; }
  .card-back { left: 879px; }
  .card-front .brand { left: 14px; top: 14px; }
  .card-front .brand-mark { width: 8px; height: 8px; }
  .card-front .brand-name { font-size: 10px; letter-spacing: 1px; }
  .card-front .brand-tagline { font-size: 5px; margin-left: 15px; }
  .card-person { position: absolute; left: 122px; top: 18px; width: 76px; text-align: center; }
  .card-person .name { color: var(--brand-red); font-size: 8px; font-weight: 500; white-space: nowrap; }
  .card-person .role { font-size: 5px; color: var(--ink-soft); }
  .card-front .card-panel {
    position: absolute; left: 0; right: 0; bottom: 0; height: 40px;
    background: linear-gradient(90deg, var(--brand-red-dark), var(--brand-red));
    color: #fff; font-size: 4.2px; line-height: 1.55; padding: 6px 9px;
    display: flex; justify-content: space-between; align-items: flex-end; gap: 6px;
    white-space: nowrap;
  }
  .card-front .card-panel .company { font-weight: 600; }
  .card-back .brand { left: 0; right: 0; top: 30px; display: flex; flex-direction: column; align-items: center; }
  .card-back .brand-mark { width: 9px; height: 9px; }
  .card-back .brand-name { font-size: 12px; letter-spacing: 1.5px; }
  .card-back .brand-tagline { font-size: 5.5px; }
  .card-back .band { height: 10px; }
  .card-back .band-orange { width: 42px; }
  .card-back .band-red { color: #fff; font-size: 5px; display: flex; align-items: center; justify-content: center; letter-spacing: .3px; }

  /* Envelope front */
  .envelope-front { left: 582px; top: 275px; width: 569px; height: 244px; }
  .envelope-front .brand { left: 36px; top: 32px; }
  .envelope-front .brand-name { font-size: 18px; }
  .envelope-front .brand-tagline { font-size: 8px; margin-left: 21px; }
  .envelope-front .corner-square { right: 22px; bottom: 30px; width: 40px; height: 40px; }
  .envelope-front .band { height: 14px; }
  .envelope-front .band-orange { width: 108px; }

  /* Envelope back */
  .envelope-back { left: 582px; top: 540px; width: 569px; height: 245px; }
  .envelope-flaps { position: absolute; inset: 0; }
  .envelope-back .brand { left: 0; right: 0; top: 30px; display: flex; justify-content: center; }
  .envelope-back .brand-name { font-size: 15px; }
  .envelope-return {
    position: absolute; left: 0; right: 0; top: 193px; text-align: center;
    font-size: 7.5px; line-height: 1.5; white-space: nowrap;
  }
  .envelope-return .company { color: var(--brand-red); font-weight: 600; font-size: 9px; }
</style>
</head>
<body>

  <section class="sheet letterhead">
    <div class="brand">
      <div class="brand-row"><span class="brand-mark"></span><span class="brand-name">BAWO</span></div>
      <div class="brand-tagline">Quality Materials, Reliable Supply</div>
    </div>
    <address class="letterhead-contact">
      <div class="company">PT Bawo Ingredients</div>
      <div>Ruko Puri Lestari Selatan</div>
      <div>Blok F07 no: 11-12</div>
      <div>Sunter Jaya Utara, 14350</div>
      <div>Indonesia</div>
      <div class="gap"></div>
      <div>Tel:+62 21 638 2097</div>
      <div>Fax:+62 21 638 2096</div>
      <div>Email: info@bawo-ingredients.co.id</div>
    </address>
    <span class="corner-square"></span>
    <div class="band"><span class="band-orange"></span><span class="band-red"></span></div>
  </section>

  <section class="sheet card card-front">
    <div class="brand">
      <div class="brand-row"><span class="brand-mark"></span><span class="brand-name">BAWO</span></div>
      <div class="brand-tagline">Quality Materials, Reliable Supply</div>
    </div>
    <div class="card-person">
      <div class="name">Dimas Pratomo</div>
      <div class="role">General Manager</div>
    </div>
    <div class="card-panel">
      <div>
        <div class="company">PT Bawo Ingredients</div>
        <div>Ruko Puri Lestari Selatan, Blok F07 no: 11-12</div>
        <div>Sunter Jaya Utara, 14350 Indonesia</div>
        <div>Tel: +62 21 638 2097 &nbsp;Fax: +62 21 638 2096</div>
      </div>
      <div style="text-align:right">
        <div>info@bawo-ingredients.co.id</div>
        <div>www.bawo-ingredients.co.id</div>
      </div>
    </div>
  </section>

  <section class="sheet card card-back">
    <div class="brand">
      <div class="brand-row"><span class="brand-mark"></span><span class="brand-name">BAWO</span></div>
      <div class="brand-tagline">Quality Materials, Reliable Supply</div>
    </div>
    <div class="band"><span class="band-orange"></span><span class="band-red">www.bawo-ingredients.co.id</span></div>
  </section>

  <section class="sheet envelope-front">
    <div class="brand">
      <div class="brand-row"><span class="brand-mark"></span><span class="brand-name">BAWO</span></div>
      <div class="brand-tagline">Quality Materials, Reliable Supply</div>
    </div>
    <span class="corner-square"></span>
    <div class="band"><span class="band-orange"></span><span class="band-red"></span></div>
  </section>

  <section class="sheet envelope-back">
    <svg class="envelope-flaps" viewBox="0 0 569 245" width="569" height="245" aria-hidden="true">
      <path d="M0 20 Q20 40 284 100 Q548 40 569 20" fill="none" stroke="var(--rule)" stroke-width="1"/>
      <path d="M0 245 L150 90" fill="none" stroke="var(--rule)" stroke-width="1"/>
      <path d="M569 245 L420 90" fill="none" stroke="var(--rule)" stroke-width="1"/>
      <line x1="190" y1="188" x2="379" y2="188" stroke="var(--brand-orange)" stroke-width="1"/>
    </svg>
    <div class="brand">
      <div class="brand-row"><span class="brand-mark"></span><span class="brand-name">BAWO</span></div>
    </div>
    <address class="envelope-return">
      <div class="company">PT Bawo Ingredients</div>
      <div>Ruko Puri Lestari Selatan, Blok F07 no: 11-12 Sunter Jaya Utara, 14350 Indonesia</div>
      <div>Tel: +62 21 638 2097 &nbsp;Fax: +62 21 638 2096 &nbsp; Email: info@bawo-ingredients.co.id</div>
    </address>
  </section>

</body>
</html>
```